A Spin Above Par Company Brochure

I am the owner of a Mobile Disc Jockey company specializing in weddings. I am looking for a Tri Fold color brochure that is modern and eye catching with the focus being on upscale wedding events. I also want it to be easy to read and not overly cluttered ! I would like it to reflect our website located at aspinabovepar.example
I also have different variations and file types of my logo such as jpeg and png files. I need some good dance floor pics. If you do not have any good stock photos I can look through my photo library. I uploaded a logo and pic I found from one of my videos. Not sure if it is worth anything.
We also do Uplighting and Photo Booths which I would like in the brochure. Much of the text copy needed can be taken from our website if needed. Please refer to the website to see what we do and our style.

Target Market(s)

upscale weddings

Industry/Entity Type

wedding dj entertainment & masters of ceremonies

Requirements
Nice to have
• nice pictures of packed dance floors and people having fun

```html
<!DOCTYPE html>
<html lang="en">
<head>
<meta charset="utf-8">
<title>A Spin Above Par – Tri-Fold Brochure</title>
<link rel="stylesheet" href="https://fonts.googleapis.com/css2?family=Montserrat:ital,wght@0,400;0,600;0,700;0,800;1,700&family=Oswald:wght@600;700&display=swap">
<style>
  :root{
    --bg:#e9e9ec;
    --purple:#6b2c9c;
    --purple-deep:#4f1a7a;
    --purple-light:#8a45b8;
    --magenta:#c8207a;
    --red:#e3173e;
    --ink:#3a3a3a;
    --dark:#1d1d1f;
    --white:#ffffff;
    --gold:#f2c230;
  }
  *{box-sizing:border-box;margin:0;padding:0}
  html,body{width:1200px;height:3000px;overflow:hidden}
  body{background:var(--bg);font-family:"Montserrat",Arial,sans-serif;color:var(--ink);position:relative}
  .spread{position:absolute;left:60px;width:1080px;height:756px;display:flex;box-shadow:0 6px 24px rgba(0,0,0,.18);background:var(--white)}
  .spread--outside{top:684px}
  .spread--inside{top:1560px}
  .panel{position:relative;width:360px;height:756px;overflow:hidden}
  .panel--purple{background:linear-gradient(180deg,var(--purple) 0%,var(--purple-deep) 100%);color:var(--white)}
  .panel--white{background:var(--white)}
  .photo{position:absolute;display:block}
  .body-copy{font-size:10.5px;line-height:1.42}
  .body-copy p{margin-bottom:12px}

  /* Outside – panel 1 */
  .intro{position:absolute;left:28px;right:28px;top:370px}
  .intro__title{font-weight:800;font-size:16px;line-height:1.3;color:var(--red);text-transform:uppercase}
  .intro__title span{color:var(--purple)}
  .intro__lede{font-weight:700;font-style:italic;font-size:11.5px;line-height:1.35;color:var(--dark);margin:10px 0 18px}
  .rule{width:100px;height:1px;background:#cfcfcf;margin-bottom:16px}

  /* Outside – panel 2 */
  .review{position:absolute;left:36px;right:24px;top:66px;height:218px;border:1.5px dashed rgba(255,255,255,.8);border-radius:10px;padding:20px 16px 10px 16px;font-size:10.5px;line-height:1.4;text-align:center}
  .review__avatar{position:absolute;left:22px;top:38px;width:62px;height:62px;border-radius:50%;border:3px solid var(--white)}
  .review__lead{padding-left:62px;margin-bottom:14px}
  .review__quote{position:absolute;left:18px;top:152px;font-family:Georgia,serif;font-size:34px;font-weight:700;line-height:1}
  .review__name{color:var(--gold);font-weight:600;margin-top:8px}
  .review__stars{color:var(--gold);letter-spacing:2px;font-size:10px}
  .booth-photo{left:50px;top:311px;width:260px;height:182px;border:3px solid var(--white)}
  .contact{position:absolute;left:0;right:0;top:528px;text-align:center;font-size:10.5px}
  .contact__title{font-weight:700;font-size:18px;margin-bottom:20px}
  .contact__title span{color:var(--red)}
  .contact__item{margin-bottom:8px;line-height:1.4}
  .contact__icon{display:block;margin:0 auto 6px}
  .contact__hours{font-weight:600;margin-top:10px}

  /* Outside – panel 3 (cover) */
  .brand{position:absolute;left:0;right:0;top:52px;display:flex;align-items:center;justify-content:center;gap:10px}
  .brand__dot{width:16px;height:16px;border-radius:50%;background:var(--purple)}
  .brand__name{font-weight:700;font-size:24px;color:#5a5a5a}
  .cover-shapes{position:absolute;left:0;top:0}
  .cover-title{position:absolute;left:0;right:0;top:212px;text-align:center;font-family:"Oswald",Impact,sans-serif;font-weight:700;font-size:38px;line-height:1.05;color:var(--magenta);text-transform:uppercase}
  .cover-title span{color:var(--red);font-size:33px}
  .cover-sub{position:absolute;left:0;right:0;top:318px;text-align:center;color:var(--white);font-size:10px;font-weight:600;line-height:1.35}
  .cover-site{position:absolute;left:0;right:0;bottom:30px;text-align:center;font-weight:600;font-size:15px;letter-spacing:1.5px;color:var(--dark)}

  /* Inside */
  .section-title{font-weight:800;font-size:22px;text-transform:uppercase;letter-spacing:.5px}
  .weddings{position:absolute;left:34px;right:26px;top:355px}
  .weddings .section-title{color:var(--purple)}
  .weddings__lede{border-left:3px solid var(--purple);padding-left:12px;margin:8px 0 16px;font-weight:600;font-size:16px;line-height:1.25;color:var(--dark)}
  .weddings__lede span{color:var(--red)}
  .corporate{position:absolute;left:34px;right:26px;top:32px}
  .corporate .section-title{margin-bottom:12px}
  .corporate .accent{color:var(--red)}
  .event-photo{left:38px;top:522px;width:284px;height:192px;border:3px solid var(--white)}
  .booth{position:absolute;left:34px;right:26px;top:32px}
  .booth .section-title{color:var(--purple);margin-bottom:12px}
</style>
</head>
<body>

<!-- Outside spread -->
<section class="spread spread--outside" aria-label="Brochure outside">
  <article class="panel panel--white">
    <svg class="photo" width="360" height="345" viewBox="0 0 360 345" role="img" aria-label="Photo of a packed dance floor under purple lighting">
      <defs><linearGradient id="floor" x1="0" y1="0" x2="0" y2="1"><stop offset="0" stop-color="#3b1f63"/><stop offset=".55" stop-color="#7a3fa8"/><stop offset="1" stop-color="#2b1840"/></linearGradient></defs>
      <polygon points="0,0 360,0 360,290 0,345" fill="url(#floor)"/>
    </svg>
    <div class="intro">
      <h2 class="intro__title">The most recommended<br><span>DJ's in Southwest Florida</span></h2>
      <p class="intro__lede">It's your day. Let us help you make<br>it happen, your way</p>
      <div class="rule"></div>
      <div class="body-copy">
        <p>Our award winning DJs are recommended by the finest venues in Naples, Fort Myers and the surrounding areas and we are known for helping our clients create the ultimate wedding entertainment experience.</p>
        <p>We offer creative ideas and a fresh approach to help you customize your event around the style &amp; vibe that you want. Planning this way is fun and eliminates the stress that comes with preparing for your special day.</p>
        <p>Are Packed dance floors, personalization, and lots of tired people smiling on their way out at the end of the night how you want your wedding to be remembered? If so, Click on the "Get started button below".</p>
      </div>
    </div>
  </article>

  <article class="panel panel--purple">
    <div class="review">
      <p class="review__lead">I am so happy I hired A Spin Above Par for our wedding day!</p>
      <p>Jordan was so fun and easy to work with — he listened to everything I wanted and delivered way above my expectations! Multiple people came up to us during and after the wedding to complement the DJ. Thank you so much Jordan for helping to make our day so amazing. The dance floor was never empty and the energy was always high! You are the best!</p>
      <p class="review__name">Lena R.</p>
      <p class="review__stars">★★★★★</p>
    </div>
    <svg class="review__avatar" viewBox="0 0 62 62" role="img" aria-label="Portrait photo of the reviewing bride"><circle cx="31" cy="31" r="31" fill="#d9b99a"/></svg>
    <span class="review__quote" aria-hidden="true">“</span>
    <svg class="photo booth-photo" viewBox="0 0 260 182" preserveAspectRatio="none" role="img" aria-label="Photo of two guests posing at a ring-light photo booth">
      <defs><linearGradient id="booth" x1="0" y1="0" x2="1" y2="1"><stop offset="0" stop-color="#1a1f3a"/><stop offset=".6" stop-color="#2f3e6e"/><stop offset="1" stop-color="#0f1222"/></linearGradient></defs>
      <rect width="260" height="182" fill="url(#booth)"/>
    </svg>
    <div class="contact">
      <h3 class="contact__title">Contact <span>us</span></h3>
      <div class="contact__item">
        <svg class="contact__icon" width="10" height="13" viewBox="0 0 10 13"><path d="M5 0a5 5 0 0 1 5 5c0 3.5-5 8-5 8S0 8.5 0 5a5 5 0 0 1 5-5z" fill="#e3173e"/><circle cx="5" cy="5" r="2" fill="#6b2c9c"/></svg>
        A Spin Above Par<br>Bayview, FL 00000
      </div>
      <div class="contact__item">
        <svg class="contact__icon" width="11" height="11" viewBox="0 0 11 11"><path d="M2 0l2 2.5-1.2 1.6a7 7 0 0 0 4.1 4.1L8.5 7 11 9l-1.5 2C4.5 11 0 6.5 0 1.5z" fill="#e3173e"/></svg>
        555.010.3648
      </div>
      <div class="contact__item">
        <svg class="contact__icon" width="13" height="9" viewBox="0 0 13 9"><rect width="13" height="9" fill="#e3173e"/><path d="M0 0l6.5 5L13 0" fill="none" stroke="#6b2c9c" stroke-width="1.2"/></svg>
        hello@aspinabovepar.example
      </div>
      <p class="contact__hours">Monday - Friday: 8:00 AM - 10:00 PM</p>
    </div>
  </article>

  <article class="panel panel--white">
    <svg class="cover-shapes" width="360" height="756" viewBox="0 0 360 756">
      <defs><linearGradient id="couple" x1="0" y1="0" x2="0" y2="1"><stop offset="0" stop-color="#2a1b14"/><stop offset=".5" stop-color="#6b4a36"/><stop offset="1" stop-color="#c9b8aa"/></linearGradient></defs>
      <polygon points="0,176 360,148 360,168 0,196" fill="var(--purple)"/>
      <polygon points="0,198 360,120 360,760 0,760" fill="var(--dark)"/>
      <g role="img" aria-label="Photo of a newlywed couple exiting through a shower of sparklers and confetti">
        <polygon points="0,372 360,372 360,600 0,680" fill="url(#couple)"/>
      </g>
      <polygon points="0,680 360,600 360,612 0,692" fill="var(--purple-light)"/>
      <polygon points="0,692 360,612 360,760 0,760" fill="var(--white)"/>
      <polygon points="120,668 360,614 360,622 120,676" fill="var(--purple)"/>
    </svg>
    <div class="brand"><span class="brand__dot"></span><span class="brand__name">A Spin Above Par</span></div>
    <h1 class="cover-title">Modern, Tasteful<br><span>&amp; Fun Entertainment</span></h1>
    <p class="cover-sub">Weddings, Corporate Events, Private Parties<br>any event is better with A Spin Above Par</p>
    <p class="cover-site">www.aspinabovepar.example</p>
  </article>
</section>

<!-- Inside spread -->
<section class="spread spread--inside" aria-label="Brochure inside">
  <article class="panel panel--white">
    <svg class="photo" width="360" height="345" viewBox="0 0 360 345" role="img" aria-label="Photo of a couple's first dance on a fog-covered ballroom floor">
      <defs><linearGradient id="firstdance" x1="0" y1="0" x2="0" y2="1"><stop offset="0" stop-color="#c9a48f"/><stop offset=".6" stop-color="#e8d6cc"/><stop offset="1" stop-color="#ffffff"/></linearGradient></defs>
      <polygon points="0,0 360,0 360,310 0,345" fill="url(#firstdance)"/>
    </svg>
    <div class="weddings">
      <h2 class="section-title">Weddings</h2>
      <p class="weddings__lede">How do you want<br>your <span>wedding remembered?</span></p>
      <div class="body-copy">
        <p>This is one of the first questions I ask couples when they contact us about wedding DJ entertainment and the response is always the same,</p>
        <p><strong>"I want a great party and everyone to leave saying it was the best wedding ever"!</strong></p>
        <p>Beginning with your initial consultation, we listen to you and respond with creative ideas and helpful advice so your event is all about you. We know it's more than just great music, it's keeping you guests engaged and coordinating with your venue and vendors for a smooth and timely event everyone will never forget.</p>
        <p>Contact us now and find out why so many couples continue to place their faith and trust in us to help them create the ultimate wedding experience.</p>
      </div>
    </div>
  </article>

  <article class="panel panel--purple">
    <div class="corporate">
      <h2 class="section-title">Corporate</h2>
      <div class="body-copy">
        <p>With over 30+ years of experience providing DJ entertainment and lighting services for corporate events and company parties, we understand how important creating the right atmosphere and delivering quality entertainment is to the success of your event. So whether you're planning a sales incentive meeting, awards presentation, beach party, holiday party or gala evening, let us help you create an event your employees will never forget.</p>
        <p>Our DJs are always ready to fill your dance floor so everyone can cut loose and enjoy a well-deserved break. If you would rather a more reserved approach, we can also provide a non-interactive style as well!</p>
        <p>We offer Monogram branding services, Photobooths and engaging interactive entertainment such as Karaoke and game show entertainment!</p>
        <p>SATISFIED CLIENTS: Fortune 500 companies such as Northwind Labs, Bluejay Air, Harbor Media Group, Golden Arc Foods, Sunfield Growers and Maple Page Publishing just to name a few.</p>
        <p>Call us now at <span class="accent">555.010.3648</span> and let us help you create your next successful corporate event or company party.</p>
      </div>
    </div>
    <svg class="photo event-photo" viewBox="0 0 284 192" preserveAspectRatio="none" role="img" aria-label="Photo of a corporate event room with red uplighting and projection screens">
      <defs><linearGradient id="corp" x1="0" y1="0" x2="0" y2="1"><stop offset="0" stop-color="#2a1016"/><stop offset=".5" stop-color="#8a2b2b"/><stop offset="1" stop-color="#1a0d10"/></linearGradient></defs>
      <rect width="284" height="192" fill="url(#corp)"/>
    </svg>
  </article>

  <article class="panel panel--white">
    <div class="booth">
      <h2 class="section-title">Photo Booth</h2>
      <div class="body-copy">
        <p>It's no secret photo booths have been a hit at weddings as well as any other event. Our photo booth offers a modern sleek look and is so simple to operate it doesn't need an attendant. However we want you and your guests to have the best experience possible so we provide one as part of our package.</p>
        <p>The combination of the right props and a fun and friendly attendant will even arouse the curiosity of your shyest guests. Once they leave the photo booth they head to the dance floor to continue the fun.</p>
        <p>It's as easy as grabbing a prop and touching the screen. Instantly we text it to your phone or email it to you. From their you can share it to any social media site you want or share it with family and friends.</p>
      </div>
    </div>
    <svg class="photo" style="left:0;top:0" width="360" height="756" viewBox="0 0 360 756" role="img" aria-label="Photo of a bride and groom walking hand in hand through a celebrating crowd">
      <defs><linearGradient id="walk" x1="0" y1="0" x2="0" y2="1"><stop offset="0" stop-color="#e6ddd6"/><stop offset=".5" stop-color="#8a7a70"/><stop offset="1" stop-color="#3b302c"/></linearGradient></defs>
      <polygon points="0,395 360,345 360,756 0,756" fill="url(#walk)"/>
    </svg>
  </article>
</section>

</body>
</html>
```